Wallet/Purse themed website design

We need a simple but visually stunning graphic design for a new web based company called "thecardvaultly.com".

TheCardVaultly is an online/phone app offering extremely secure backup/storage for our users' personal documentation, such as credit cards, ID, passports, certificates, insurance etc.

Documents will be uploaded via a mobile app (initially zPad) to the storage. Retrieval is only possible via login together with bank level authentication (using personal questions).

Our service will not prevent the theft of our customer's physical wallet however our retrieval service can be accessed anywhere online and assist with the replacement. (for example a lost passport will require a new passport request which requires details of the lost passport number/details).
The key audiences for TheCardVaultly include holidaymakers, businessmen, individuals, banking customers

We have specified that the initial design needs only to have 3 pages - home page, login page, wallet contents retrieval page.

Common themes of the following should be strongly brought to bear on the pages:
-Leather wallet/stitching
-Secure/safe/private/encryted
-Personal - for example family holiday
-Access anywhere
-Pick pockets can easily steal your wallet
Updates

Thank you for all of your submissions!  This was our first attempt to source a design via Pixel Bazaar and we will certainly use this resource again.

Thank you.

Target Market(s)

Industry/Entity Type

Graphic Design

Requirements
Must have
• 3 pages - home page, login page, wallet contents retrieval page.
Nice to have
• Modern UI design appealing to families and individuals

```html
<!DOCTYPE html>
<html lang="en">
<head>
<meta charset="utf-8">
<title>Card Vaultly – Page Designs</title>
<link rel="stylesheet" href="https://fonts.googleapis.com/css2?family=Cabin:wght@500;600&display=swap">
<style>
  :root {
    --backdrop: #0151a0;
    --panel: #f26823;
    --accent: #0c4f9e;
    --field: #ffffff;
    --ink: #ffffff;
  }
  * { box-sizing: border-box; margin: 0; padding: 0; }
  html, body { width: 1200px; height: 900px; overflow: hidden; }
  body {
    background: var(--backdrop);
    font-family: "Cabin", sans-serif;
    color: var(--ink);
    position: relative;
  }
  .page {
    position: absolute;
    top: 156px;
    height: 556px;
    background: var(--panel);
  }
  .page--backup { left: 76px; width: 342px; }
  .page--login { left: 436px; width: 327px; }
  .page--home { left: 780px; width: 337px; }

  .page__title {
    position: absolute;
    top: 12px;
    font-size: 31px;
    font-weight: 500;
    white-space: nowrap;
  }
  .page__icon { position: absolute; }

  .page--backup .page__title { left: 17px; }
  .page--backup .page__icon { left: 255px; top: 2px; }
  .upload-area {
    position: absolute;
    left: 26px; top: 90px;
    width: 289px; height: 265px;
    background: var(--field);
  }
  .share-icons {
    position: absolute;
    left: 0; top: 380px; width: 100%;
  }
  .share-icons svg { position: absolute; top: 0; }
  .footer-nav {
    position: absolute;
    left: 0; top: 514px; width: 100%;
    font-size: 19px; font-weight: 600;
  }
  .footer-nav span { position: absolute; }

  .page--login .page__title { left: 18px; }
  .page--login .page__icon { left: 224px; top: 6px; }
  .field-label {
    position: absolute;
    left: 7px;
    font-size: 25px; font-weight: 500;
  }
  .field-input {
    position: absolute;
    left: 143px; width: 172px; height: 30px;
    background: var(--field);
  }
  .button {
    position: absolute;
    background: var(--accent);
    font-size: 25px; font-weight: 500;
    text-align: center;
    line-height: 31px; height: 31px;
  }
  .page--login .button { left: 85px; top: 324px; width: 132px; }

  .page--home .page__title { left: 32px; }
  .page--home .page__icon { left: 232px; top: 6px; }
  .info-label {
    position: absolute;
    left: 34px;
    font-size: 25px; font-weight: 500;
  }
  .page--home .button { width: 132px; }
</style>
</head>
<body>

  <section class="page page--backup">
    <h2 class="page__title">Card Vaultly</h2>
    <svg class="page__icon" width="86" height="58" viewBox="0 0 86 58" fill="none" stroke="#0c4f9e" stroke-width="4">
      <path d="M86 8 L66 10 L62 38 L10 38"/>
      <path d="M5 12 H66 L64 30 H12 Z" stroke-width="3"/>
      <path d="M18 12 V30 M30 12 V30 M42 12 V30 M54 12 V30 M8 21 H65" stroke-width="3"/>
      <circle cx="18" cy="48" r="5" fill="#0c4f9e"/>
      <circle cx="58" cy="48" r="5" fill="#0c4f9e"/>
    </svg>
    <div class="upload-area" role="img" aria-label="Uploaded wallet document preview"></div>
    <div class="share-icons">
      <svg style="left:14px" width="68" height="40" viewBox="0 0 68 40" fill="none" stroke="#fff" stroke-width="3">
        <rect x="2" y="2" width="64" height="36" fill="#fff" stroke="none"/>
        <path d="M2 2 L34 24 L66 2 M2 38 L26 18 M66 38 L42 18" stroke="#f26823"/>
      </svg>
      <svg style="left:112px" width="58" height="44" viewBox="0 0 58 44" fill="none" stroke="#fff" stroke-width="3">
        <ellipse cx="29" cy="22" rx="26" ry="20"/>
        <ellipse cx="29" cy="22" rx="11" ry="20"/>
        <path d="M3 22 H55 M7 12 H51 M7 32 H51 M29 2 V42"/>
      </svg>
      <svg style="left:190px" width="66" height="48" viewBox="0 0 66 48" fill="none" stroke="#fff" stroke-width="3">
        <ellipse cx="24" cy="22" rx="21" ry="19"/>
        <ellipse cx="24" cy="22" rx="9" ry="19"/>
        <path d="M3 22 H45 M6 12 H42 M6 32 H42 M24 3 V41"/>
        <circle cx="38" cy="28" r="10" fill="#f26823" stroke-width="4"/>
        <path d="M45 35 L62 46" stroke-width="6"/>
      </svg>
      <svg style="left:268px" width="38" height="46" viewBox="0 0 38 46" fill="none" stroke="#fff" stroke-width="3">
        <ellipse cx="19" cy="23" rx="16" ry="20"/>
        <path d="M19 12 V34 M8 23 H30" stroke-width="5"/>
      </svg>
    </div>
    <nav class="footer-nav">
      <span style="left:12px">Contact</span>
      <span style="left:140px">About Us</span>
      <span style="left:279px">Store</span>
    </nav>
  </section>

  <section class="page page--login">
    <h2 class="page__title">Secure Login</h2>
    <svg class="page__icon" width="96" height="52" viewBox="0 0 96 52" fill="#0c4f9e">
      <path d="M2 20 H58 V34 H50 L46 40 L40 34 L34 40 L28 34 L4 34 Z"/>
      <ellipse cx="74" cy="26" rx="21" ry="24"/>
      <circle cx="80" cy="18" r="5" fill="#f26823"/>
    </svg>
    <span class="field-label" style="top:58px">Username</span>
    <div class="field-input" style="top:88px"></div>
    <span class="field-label" style="top:112px">Password</span>
    <div class="field-input" style="top:140px"></div>
    <span class="field-label" style="top:167px">Question</span>
    <div class="field-input" style="top:196px"></div>
    <span class="field-label" style="top:224px">Answers</span>
    <div class="field-input" style="top:253px"></div>
    <div class="button">Submit</div>
  </section>

  <section class="page page--home">
    <h2 class="page__title">Home Page</h2>
    <svg class="page__icon" width="64" height="46" viewBox="0 0 64 46" fill="none" stroke="#fff" stroke-width="3">
      <path d="M2 20 L32 3 L62 20"/>
      <path d="M8 17 V44 H56 V17"/>
      <rect x="14" y="24" width="12" height="9"/>
      <rect x="38" y="24" width="12" height="9"/>
      <rect x="27" y="33" width="10" height="11"/>
      <path d="M44 8 V3 H50 V12"/>
    </svg>
    <span class="info-label" style="top:86px">Name</span>
    <span class="info-label" style="top:140px">Details</span>
    <div class="button" style="left:24px; top:196px">Back</div>
    <div class="button" style="left:179px; top:194px">Next</div>
    <div class="button" style="left:24px; top:279px">Edit</div>
    <div class="button" style="left:179px; top:276px">Delete</div>
  </section>

</body>
</html>
```